Lumavento business card

We need a modern business card - With our 4 colors - See web: www.lumavento.dk

I have attached logo and som old business Cards we have - Lets Make the new ones shine...:-) -

Industry/Entity Type

Business

Requirements
Must have
• the logo with lumavento only,

```html
<!DOCTYPE html>
<html lang="da">
<head>
<meta charset="utf-8">
<title>Lumavento – visitkort</title>
<link rel="stylesheet" href="https://fonts.googleapis.com/css2?family=Source+Sans+3:wght@400;600;700&display=swap">
<style>
  :root {
    --pink: #ec008c;
    --lime: #a8c93a;
    --plum: #731878;
    --orange: #f58220;
    --white: #ffffff;
    --backdrop: #ece8e4;
  }
  * { box-sizing: border-box; margin: 0; padding: 0; }
  html, body {
    width: 1200px; height: 900px; overflow: hidden;
    background: var(--backdrop);
    font-family: "Source Sans 3", sans-serif;
  }
  .canvas { position: relative; width: 1200px; height: 900px; }
  .card {
    position: absolute; overflow: hidden;
    box-shadow: 0 4px 14px rgba(0,0,0,.18);
  }
  /* Front */
  .card-front {
    left: 238px; top: 62px; width: 555px; height: 342px;
    background: var(--pink);
  }
  .card-front .accent-area { position: absolute; left: 0; top: 0; width: 555px; height: 295px; }
  .contact { position: absolute; left: 37px; top: 44px; color: var(--white); }
  .contact-name { font-size: 21px; font-weight: 700; line-height: 1.1; }
  .contact-role { font-size: 15px; font-weight: 400; margin-top: 3px; }
  .contact-list { list-style: none; margin-top: 22px; font-size: 15px; }
  .contact-list li { display: flex; align-items: center; height: 23.5px; }
  .contact-list svg { width: 12px; height: 12px; margin-right: 11px; fill: var(--white); }
  .address-band {
    position: absolute; left: 0; bottom: 0; width: 100%; height: 47px;
    background: var(--orange); color: var(--white);
    display: flex; align-items: center; justify-content: center;
    font-size: 15.5px; font-weight: 400;
  }
  /* Back */
  .card-back {
    left: 457px; top: 518px; width: 560px; height: 343px;
    background: var(--plum); color: var(--white); text-align: center;
  }
  .brand-dot {
    position: absolute; left: 256px; top: 86px; width: 48px; height: 48px;
    border-radius: 50%; background: var(--white);
  }
  .brand-name {
    position: absolute; left: 0; right: 0; top: 194px;
    font-size: 23px; font-weight: 400; letter-spacing: 4px;
  }
  .brand-rule {
    position: absolute; left: 143px; top: 238px; width: 273px; height: 3px;
    background: var(--white);
  }
  .brand-tagline {
    position: absolute; left: 0; right: 0; top: 254px;
    font-size: 16px; font-weight: 400;
  }
</style>
</head>
<body>
<main class="canvas">
  <section class="card card-front">
    <svg class="accent-area" viewBox="0 0 555 295" role="img" aria-label="Lime green graphic area with plum edge">
      <polygon points="505,0 555,0 555,295 160,295" fill="var(--lime)"/>
      <polyline points="505,0 160,295" stroke="var(--plum)" stroke-width="16" fill="none"/>
    </svg>
    <div class="contact">
      <h1 class="contact-name">Sune Valdorf</h1>
      <p class="contact-role">Salgsdirektor</p>
      <ul class="contact-list">
        <li><svg viewBox="0 0 24 24"><path d="M6.6 10.8a15.1 15.1 0 0 0 6.6 6.6l2.2-2.2c.3-.3.7-.4 1-.2 1.1.4 2.3.6 3.6.6.6 0 1 .4 1 1V20c0 .6-.4 1-1 1A17 17 0 0 1 3 4c0-.6.4-1 1-1h3.5c.6 0 1 .4 1 1 0 1.3.2 2.5.6 3.6.1.3 0 .7-.2 1z"/></svg>+45 20 30 40 55</li>
        <li><svg viewBox="0 0 24 24"><path d="M2 5h20v14H2zm2 2v.5l8 5 8-5V7z"/></svg>sv@lumavento.dk</li>
        <li><svg viewBox="0 0 24 24"><circle cx="12" cy="12" r="10"/></svg>www.lumavento.dk</li>
      </ul>
    </div>
    <p class="address-band">Solsikkevej 14 - 2000 Frederiksberg -Tlf. 38 12 34 56</p>
  </section>

  <section class="card card-back">
    <span class="brand-dot"></span>
    <p class="brand-name">lumavento</p>
    <span class="brand-rule"></span>
    <p class="brand-tagline">Medier til unge</p>
  </section>
</main>
</body>
</html>
```